Brindle Sky Port needs a new upscale business card design for our high end aircraft hangar complex

Brindle Sky Port (BSP) is a large, upscale jet hangar complex in the US housing expensive aircraft. We need a new business card design, using our current logo. We will be attending a industry convention and need a card design that will stand out and be remembered by aircraft owners and private pilots.

Target Market(s)

Aircraft pilots or owners looking for a new upscale hangar

Industry/Entity Type

Airport

Contact Information for Business Card

I like to use very heavy card stock, 400#, double sided. Square, no rounded edges please.

Colors
3276b5
0255a3
85abd2

Requirements
Must have
• An expensive, classy design, vivid colors.
Nice to have
• Needs to look very expensive and classy, and have some "pop". Designer must be able to download or copy my current typeface or fonts.
• One card side might be black with the "Logo and Brindle Sky Port Double line image in blue (or try gold, or glossy black), and perhaps have a grayed out "K720 jet silhouette". The other card side would have our contact info, and perhaps the "BSP Logo only". I'd like my contact info 'stacked', not in a paragraph format.
Should not have
• Should not look "too busy". Having a double-sided card will help.

```html
<!DOCTYPE html>
<html lang="en">
<head>
<meta charset="UTF-8">
<title>Brindle Sky Port – Business Card</title>
<link href="https://fonts.googleapis.com/css2?family=Montserrat:wght@400;500;600;800&display=swap" rel="stylesheet">
<style>
  :root {
    --navy: #0f3b66;
    --brand-blue: #0255a3;
    --mid-blue: #3276b5;
    --light-blue: #85abd2;
    --ink: #1d3f66;
    --paper: #ffffff;
    --backdrop: #e4e6ea;
  }
  * { margin: 0; padding: 0; box-sizing: border-box; }
  html, body {
    width: 1200px; height: 900px; overflow: hidden;
    background: var(--backdrop);
    font-family: "Montserrat", sans-serif;
  }
  .canvas {
    width: 1200px; height: 900px;
    display: flex; flex-direction: column;
    align-items: center; justify-content: center; gap: 56px;
  }
  .card {
    position: relative;
    width: 660px; height: 377px;
    border-radius: 0;
    overflow: hidden;
    box-shadow: 0 10px 30px rgba(0,0,0,0.18);
  }

  /* Front */
  .card--front {
    background: var(--navy);
    color: #fff;
    display: flex; flex-direction: column; align-items: center; justify-content: center;
    gap: 18px;
  }
  .wordmark {
    font-weight: 800; text-transform: uppercase; text-align: center;
    line-height: 1.05; letter-spacing: 1px;
  }
  .card--front .wordmark { font-size: 40px; color: #fff; }
  .card--front .website { font-size: 17px; font-weight: 500; letter-spacing: 0.5px; }

  /* Back */
  .card--back { background: var(--paper); color: var(--ink); }
  .jet-photo {
    position: absolute; left: 230px; top: 40px; width: 330px; height: 255px;
    background: radial-gradient(ellipse at 50% 55%, #d9dde2 0%, #eceef1 45%, rgba(255,255,255,0) 75%);
  }
  .card--back .wordmark {
    position: absolute; left: 40px; top: 96px;
    font-size: 30px; color: var(--brand-blue); text-align: left;
  }
  .name-block {
    position: absolute; right: 60px; top: 92px; text-align: right;
  }
  .name { font-size: 23px; font-weight: 600; color: var(--ink); }
  .role { font-size: 13px; color: var(--mid-blue); margin-top: 2px; }
  .rule { position: absolute; height: 1.5px; background: var(--mid-blue); }
  .rule--name { right: 40px; top: 150px; width: 340px; }
  .rule--contact { left: 36px; top: 250px; width: 330px; }
  .contacts {
    position: absolute; left: 40px; top: 262px;
    list-style: none; font-size: 15px; line-height: 21px; color: var(--ink);
  }
  .contacts li { display: flex; align-items: center; gap: 10px; }
  .contacts svg { width: 12px; height: 12px; fill: var(--mid-blue); flex: none; }
  .base-band { position: absolute; left: 0; bottom: 0; width: 660px; height: 80px; }
</style>
</head>
<body>
<main class="canvas">

  <section class="card card--front" aria-label="Card front">
    <div class="wordmark">Brindle<br>Sky Port</div>
    <div class="website">www.brindleskyport.com</div>
  </section>

  <section class="card card--back" aria-label="Card back">
    <div class="jet-photo" role="img" aria-label="Faded photograph of a private jet, front view"></div>

    <div class="wordmark">Brindle<br>Sky Port</div>

    <div class="name-block">
      <div class="name">Marlo Pendry</div>
      <div class="role">Director</div>
    </div>
    <div class="rule rule--name"></div>
    <div class="rule rule--contact"></div>

    <ul class="contacts">
      <li><svg viewBox="0 0 24 24"><path d="M6.6 10.8a15 15 0 0 0 6.6 6.6l2.2-2.2c.3-.3.7-.4 1-.2 1.1.4 2.300.6 3.6.6.6 0 1 .4 1 1V20c0 .6-.4 1-1 1A17 17 0 0 1 3 4c0-.6.4-1 1-1h3.5c.6 0 1 .4 1 1 0 1.3.2 2.5.6 3.6.1.3 0 .7-.2 1z"/></svg>+041 3815-2290</li>
      <li><svg viewBox="0 0 24 24"><path d="M3 9c0-3 4-5 9-5s9 2 9 5v2h-5V9H8v2H3zM6 13h12l2 7H4z"/></svg>+041 3815-4471</li>
      <li><svg viewBox="0 0 24 24"><path d="M2 5h20v14H2zm2 2v.5l8 5 8-5V7zm0 2.8V17h16V9.8l-8 5z"/></svg>info@brindleskyport.com</li>
      <li><svg viewBox="0 0 24 24"><path d="M12 2a10 10 0 1 0 0 20 10 10 0 0 0 0-20zm6.9 9h-3a15 15 0 0 0-1.3-6 8 8 0 0 1 4.3 6zM12 4c.9 1.3 1.7 3.8 1.9 7h-3.8C10.3 7.8 11.1 5.3 12 4zM9.4 5a15 15 0 0 0-1.3 6h-3A8 8 0 0 1 9.4 5zM5.1 13h3a15 15 0 0 0 1.3 6 8 8 0 0 1-4.3-6zM12 20c-.9-1.3-1.700-3.8-1.9-7h3.8c-.2 3.2-1 5.7-1.9 7zm2.6-1a15 15 0 0 0 1.3-6h3a8 8 0 0 1-4.3 6z"/></svg>www.brindleskyport.com</li>
    </ul>

    <svg class="base-band" viewBox="0 0 660 80" aria-hidden="true">
      <polygon points="0,70 410,70 415,62 660,62 660,80 0,80" fill="var(--mid-blue)"/>
      <polygon points="470,20 660,20 660,80 450,80" fill="var(--navy)"/>
    </svg>
  </section>

</main>
</body>
</html>
```